Design a "healthy, happy dog and cat" cheque/check background

I am looking for a few design concepts featuring a happy healthy dog and cat, that will be used as the background of a paper cheque/check.

This will require Photoshop and stock photos.

Here is the design brief: https://docs.plinvaro.com/document/d/4Rt8mKx2LqW9zVbN3cHy7TfJ1sDp6GaE0uYoZiXeMwnB/edit?usp=sharing

Colors

Designer to choose colors to be used in the design.

Requirements
Must have
• A happy dog and cat the main focus within the "empty" central part of the cheque/check, and a complementary background for the rest of the cheque, following the design guidelines in the attached plinvaro doc.

```html
<!DOCTYPE html>
<html lang="en">
<head>
<meta charset="utf-8">
<title>Personal Cheque – Dog and Cat</title>
<link rel="stylesheet" href="https://fonts.googleapis.com/css2?family=Arimo:wght@400;700&family=Share+Tech+Mono&display=swap">
<style>
  :root {
    --page: #ffffff;
    --ink: #111111;
    --blue-deep: #2b86d2;
    --blue-mid: #6db8ec;
    --blue-light: #d9effc;
    --field: #ffffff;
    --rule: #222222;
    --pet-grey: #a9aeb5;
    --pet-tan: #d9a36e;
  }
  * { margin: 0; padding: 0; box-sizing: border-box; }
  html, body {
    width: 1200px; height: 544px; overflow: hidden;
    background: var(--page);
    font-family: "Arimo", Arial, sans-serif;
    color: var(--ink);
  }
  .canvas { position: relative; width: 1200px; height: 544px; }
  .cheque {
    position: absolute; left: 24px; top: 0; width: 1152px; height: 406px;
    background:
      radial-gradient(ellipse 420px 260px at 620px 150px, var(--blue-light) 0%, rgba(217,239,252,0) 100%),
      linear-gradient(110deg, var(--blue-deep) 0%, var(--blue-mid) 35%, var(--blue-mid) 65%, var(--blue-deep) 100%);
  }
  .pets-photo {
    position: absolute; left: 290px; top: 60px; width: 600px; height: 325px;
    background: linear-gradient(90deg, rgba(169,174,181,0) 0%, rgba(169,174,181,.55) 25%, rgba(217,163,110,.55) 65%, rgba(217,163,110,0) 100%);
    border-radius: 40%;
    filter: blur(14px);
  }
  .abs { position: absolute; white-space: nowrap; }
  .account-holder { left: 58px; top: 62px; font-size: 20px; font-weight: 700; }
  .holder-address { left: 58px; top: 85px; font-size: 18px; line-height: 22px; }
  .cheque-number { left: 1022px; top: 46px; font-size: 22px; font-weight: 700; }
  .date-label { left: 783px; top: 110px; font-size: 20px; }
  .date-boxes { left: 849px; top: 91px; display: flex; gap: 2px; }
  .date-boxes span { width: 37px; height: 36px; background: var(--field); display: block; }
  .date-format { left: 849px; top: 131px; display: flex; gap: 2px; font-size: 14px; }
  .date-format span { width: 37px; text-align: center; }
  .payee-label { left: 58px; top: 190px; font-size: 14px; line-height: 14px; }
  .dollar-sign { left: 948px; top: 183px; font-size: 32px; }
  .amount-box { left: 972px; top: 175px; width: 194px; height: 47px; background: var(--field); }
  .amount-words { left: 918px; top: 253px; font-size: 15px; }
  .institution-mark { left: 70px; top: 290px; width: 66px; height: 66px; border-radius: 50%; background: var(--ink); }
  .institution-name { left: 154px; top: 299px; font-size: 18px; font-weight: 700; }
  .institution-address { left: 154px; top: 320px; font-size: 18px; line-height: 20px; }
  .company-name { left: 808px; top: 333px; font-size: 14px; }
  .memo-label { left: 60px; top: 382px; font-size: 12px; }
  .security-badge { left: 1160px; top: 268px; width: 16px; height: 137px; border: 1px solid #333; background: #e8eef3; }
  .micr-line { left: 52px; top: 448px; font-family: "Share Tech Mono", monospace; font-size: 30px; letter-spacing: 3px; }
  .rules { position: absolute; left: 0; top: 0; }
</style>
</head>
<body>
<main class="canvas">
  <section class="cheque">
    <div class="pets-photo" role="img" aria-label="Photograph of a grey kitten and a bulldog puppy touching noses"></div>
  </section>

  <svg class="rules" width="1200" height="544" aria-hidden="true">
    <g stroke="var(--rule)" stroke-width="1.2" fill="none">
      <polyline points="58,222 922,222 922,190"/>
      <polyline points="58,275 905,275 912,240"/>
      <line x1="58" y1="398" x2="585" y2="398"/>
      <line x1="685" y1="398" x2="1100" y2="398"/>
    </g>
  </svg>

  <div class="abs account-holder">NRVC - Brightleaf Cheques Personal Cheque</div>
  <div class="abs holder-address">15 Residential Street<br>Toronto, Ontario M1M 1M1</div>
  <div class="abs cheque-number">101</div>

  <div class="abs date-label">DATE</div>
  <div class="abs date-boxes"><span></span><span></span><span></span><span></span><span></span><span></span><span></span><span></span></div>
  <div class="abs date-format"><span>D</span><span>D</span><span>M</span><span>M</span><span>Y</span><span>Y</span><span>Y</span><span>Y</span></div>

  <div class="abs payee-label">PAY TO THE<br>ORDER OF</div>
  <div class="abs dollar-sign">$</div>
  <div class="abs amount-box"></div>
  <div class="abs amount-words">100 DOLLARS</div>

  <div class="abs institution-mark"></div>
  <div class="abs institution-name">Your Financial Institution</div>
  <div class="abs institution-address">200 Finance Avenue<br>Your City, Your Province A1B 2CS</div>

  <div class="abs company-name">Optional Company Name</div>
  <div class="abs memo-label">MEMO</div>
  <div class="abs security-badge"></div>

  <div class="abs micr-line">⑈101⑈ ⑆12345⑉678⑆ 12345⑉6789⑈</div>
</main>
</body>
</html>
```